Gift voucher for a photo shoot, folding card DIN long (21 x 9.8 cm)

Hello, I'm a professional photographer and need a new design for my gift voucher card for a photo shoot. The design should be applicable to all types of photo shoots (neutral). I prefer a sophisticated design. The folded card should be printed on both sides.
My data should be included: Logo, Address: Moltkener Strße 27, 07548 Gera, Email: fotograf@tobiaswinkel.eu, Website: www.tobiaswinkel.eu Tel.: 0174 / 5839026
Updates

Please design the folding card in DIN long format (105 x 210 mm, landscape format). The card should open horizontally. Please design the front with the words "Gift voucher for you" and my logo. Please make the logo small – the words "Gift voucher" should be in the foreground.
The colors - use elegant gray with gold or white font color.
The inside should contain the words: Photo shoot for ........ worth .....€, as well as my logo.
My contact details should be on the back.

Target Market(s)

Private customer

Colors

Designer to choose only greyscale colors for use in the design.

Requirements
Must have
• Noble appearance, a gift voucher that one likes to give away, words: Gift voucher for you, photo shoot for ..., worth .......€
Nice to have
• Noble appearance of the gift voucher, a gift voucher that you like to give away
Should not have
• no pictures

```html
<!DOCTYPE html>
<html lang="de">
<head>
<meta charset="utf-8">
<title>Geschenkgutschein – Tobias Winkel Fotograf</title>
<link href="https://fonts.googleapis.com/css2?family=Cinzel:wght@400;500&family=Lato:wght@300;400&display=swap" rel="stylesheet">
<style>
  :root{
    --bg-top:#bdbdbd;
    --bg-bottom:#e4e4e4;
    --paper:#ffffff;
    --paper-shade:#ececec;
    --ink:#2b2b2b;
    --grey-text:#a9a9a9;
    --grey-head:#9a9a9a;
    --gold:#d9a24a;
    --gold-dark:#c8862a;
    --gold-light:#f2d48e;
    --bow:#ecd6b6;
  }
  *{box-sizing:border-box;margin:0;padding:0}
  html,body{width:1200px;height:711px;overflow:hidden}
  body{
    background:linear-gradient(180deg,var(--bg-top) 0%,var(--bg-bottom) 100%);
    font-family:"Lato",sans-serif;
    position:relative;
  }
  .spread{
    position:absolute;top:226px;width:540px;height:258px;
    display:flex;box-shadow:0 14px 30px rgba(0,0,0,.18);
  }
  .spread--outside{left:36px}
  .spread--inside{left:624px}
  .panel{position:relative;width:270px;height:100%;background:var(--paper);overflow:hidden}

  /* ribbons */
  .ribbon{position:absolute;left:0;right:0;height:5px}
  .ribbon--back{top:96px;background:linear-gradient(90deg,var(--gold) 0%,var(--gold-dark) 40%,var(--gold-light) 100%)}
  .ribbon--front{top:96px;background:linear-gradient(90deg,#e7c99a 0%,var(--gold-light) 70%,#e6b45e 100%)}
  .fold-band{position:absolute;top:0;bottom:0;right:0;width:3px;
    background:linear-gradient(180deg,var(--gold-light),var(--gold-dark))}
  .bow{position:absolute;top:76px;left:236px;width:68px;height:66px;z-index:2;border-radius:50%;
    background:radial-gradient(ellipse at 50% 40%,#f3e4cc 0%,var(--bow) 45%,rgba(236,214,182,0) 72%);}

  /* back panel contacts */
  .contacts{position:absolute;right:26px;bottom:16px;list-style:none;text-align:right}
  .contacts li{display:flex;justify-content:flex-end;align-items:center;gap:7px;
    font-size:9.5px;font-weight:300;color:var(--grey-text);line-height:16px;white-space:nowrap}
  .contacts svg{width:9px;height:10px;flex:none}

  /* front panel */
  .panel--front{background:linear-gradient(100deg,#f0f0f0 0%,#ffffff 45%,#f6f6f6 100%)}
  .brand{position:absolute;top:30px;left:0;right:0;text-align:center}
  .brand__mark{display:block;width:22px;height:22px;margin:0 auto 6px;border:1.5px solid var(--ink);border-radius:50%}
  .brand__name{font-family:"Cinzel",serif;font-weight:500;font-size:13px;letter-spacing:.5px;color:var(--ink);white-space:nowrap}
  .headline{position:absolute;top:132px;left:0;right:0;text-align:center;
    font-family:"Cinzel",serif;font-weight:500;font-size:26px;line-height:27px;color:var(--grey-head)}
  .headline__accent{color:var(--gold)}
  .front-rule{position:absolute;left:28px;right:20px;top:224px;height:1px;background:var(--gold-light)}
  .website{position:absolute;bottom:9px;left:0;right:0;text-align:center;font-size:8.5px;
    letter-spacing:1.6px;color:var(--grey-text)}

  /* inside */
  .panel--inside-right{background:linear-gradient(90deg,var(--paper-shade) 0%,#fafafa 50%,#f4f4f4 100%)}
  .ribbon--inside{top:46px;height:6px;background:linear-gradient(90deg,var(--gold-dark),var(--gold) 50%,var(--gold-light))}
  .inside-fields{position:absolute;inset:0;pointer-events:none}
  .field{position:absolute;left:20px;display:flex;align-items:flex-end;gap:6px;
    font-family:"Cinzel",serif;font-size:10px;letter-spacing:.8px;color:var(--grey-text)}
  .field__line{border-bottom:1.5px dotted #b9b9b9;height:8px}
  .field--shoot{top:104px}
  .field--shoot .field__line{width:370px}
  .field--value{top:140px}
  .field--value .field__line{width:400px}
  .inside-brand{position:absolute;left:40px;bottom:34px;display:flex;align-items:center;gap:8px}
  .inside-brand .brand__mark{margin:0;width:18px;height:18px}
</style>
</head>
<body>

<section class="spread spread--outside" aria-label="Außenseite">
  <div class="panel panel--back">
    <div class="ribbon ribbon--back"></div>
    <div class="fold-band"></div>
    <ul class="contacts">
      <li>0174 / 5839026
        <svg viewBox="0 0 9 10"><rect x="2" y="0.5" width="5" height="9" rx="1" fill="none" stroke="#d9a24a"/></svg></li>
      <li>Moltkener Strße 27, 07548 Gera
        <svg viewBox="0 0 9 10"><path d="M4.5 9.5C2 6.5 1 5 1 3.5a3.5 3.5 0 0 1 7 0C8 5 7 6.5 4.5 9.5z" fill="none" stroke="#d9a24a"/></svg></li>
      <li>fotograf@tobiaswinkel.eu
        <svg viewBox="0 0 9 10"><rect x="0.5" y="2" width="8" height="6" fill="none" stroke="#d9a24a"/><path d="M0.5 2l4 3.5 4-3.5" fill="none" stroke="#d9a24a"/></svg></li>
    </ul>
  </div>
  <div class="panel panel--front">
    <div class="ribbon ribbon--front"></div>
    <div class="brand">
      <span class="brand__mark"></span>
      <span class="brand__name">Tobias Winkel</span>
    </div>
    <h1 class="headline">Geschenk<br>Gutschein<br><span class="headline__accent">Für</span> Dich</h1>
    <div class="front-rule"></div>
    <p class="website">www.tobiaswinkel.eu</p>
  </div>
  <div class="bow" role="img" aria-label="Goldene Geschenkschleife über dem Falz"></div>
</section>

<section class="spread spread--inside" aria-label="Innenseite">
  <div class="panel panel--inside-left">
    <div class="ribbon ribbon--inside"></div>
    <div class="inside-brand">
      <span class="brand__mark"></span>
      <span class="brand__name">Tobias Winkel</span>
    </div>
  </div>
  <div class="panel panel--inside-right">
    <div class="ribbon ribbon--inside"></div>
  </div>
  <div class="inside-fields">
    <div class="field field--shoot"><span>Fotoshooting für</span><span class="field__line"></span></div>
    <div class="field field--value"><span>Im Wert von</span><span class="field__line"></span><span>€</span></div>
  </div>
</section>

</body>
</html>
```